Real Estate Company Looking for Business Card Designs for 3 Executives

Hello!
Thanks so much for considering our project! We are a real estate investment company located in Edmonton, Alberta called Bellhaven Group of Companies. We invest/develop both commercial and residential real estate and are looking to create 3 DOUBLE-SIDED business cards for 3 top executives in the company! (for some reason it won't let us select the double-sided option, but yes, the cards are double sided and would be happy to tip extra)

We have certain guidelines that we want our business cards to for sure follow - the back of the Business card has to be the Black Background Version of the Logo which has already been designed and linked as a file (first file). We want the entire back of the card to simply just be the black background logo. In terms of the front of the card, would like to see a smaller version of the white background logo (linked as the second file) in the top left hand corner - of course, feel free to get creative and we can make revisions together along the way! and Then after that, just text. We want the card to be sharp, clean, easy on the eyes and highly professional looking. We would like the card to include the Full name of the Company (Bellhaven Group of Companies), Name of the Person, Title, Phone, Email. If possible please provide the front part of the card for 3 people:

1) Bellhaven Group of Companies, Liora Quenby, Chief Financial Officer, 780-555-0142, lioraquenby@bellhavengroup.example

2) Bellhaven Group of Companies, Tobias Quenby, Chief Executive Officer, 780-555-0187, tobiasquenby@bellhavengroup.example

3) Bellhaven Group of Companies, Rui Delcourt, Chief Operations Officer, 587-555-0163, ruidelcourt@bellhavengroup.example

Thank you so much for considering our project & we look forward to seeing your designs!

```html
<!DOCTYPE html>
<html lang="en">
<head>
<meta charset="utf-8">
<title>Bellhaven Business Card</title>
<link href="https://fonts.googleapis.com/css2?family=Montserrat:wght@500;800&family=Lato:wght@400;700&display=swap" rel="stylesheet">
<style>
  :root {
    --ink: #0f0a0c;
    --paper: #ffffff;
    --stage: #2a2a2a;
    --pattern-dark: #120c0f;
    --pattern-light: #221a1e;
    --muted: #1c1c1c;
  }
  html, body {
    margin: 0;
    width: 1200px;
    height: 1015px;
    overflow: hidden;
    background: var(--stage);
  }
  .card {
    position: absolute;
    left: 220px;
    width: 760px;
    height: 434px;
    overflow: hidden;
    box-shadow: 0 10px 30px rgba(0,0,0,.45);
  }
  /* Back of card */
  .card-back {
    top: 40px;
    background: var(--ink);
  }
  .card-back .texture {
    position: absolute;
    inset: 0;
    background: linear-gradient(135deg, var(--pattern-light), var(--pattern-dark) 60%, var(--ink));
  }
  .card-back .wordmark {
    position: absolute;
    inset: 0;
    display: flex;
    align-items: center;
    justify-content: center;
    font-family: "Montserrat", sans-serif;
    font-weight: 500;
    font-size: 60px;
    letter-spacing: 12px;
    color: var(--paper);
  }
  /* Front of card */
  .card-front {
    top: 534px;
    background: var(--paper);
  }
  .card-front .wave {
    position: absolute;
    inset: 0;
  }
  .card-front .wordmark {
    position: absolute;
    left: 70px;
    top: 150px;
    font-family: "Montserrat", sans-serif;
    font-weight: 500;
    font-size: 38px;
    letter-spacing: 8px;
    color: var(--ink);
  }
  .identity {
    position: absolute;
    right: 48px;
    top: 30px;
    text-align: right;
  }
  .identity .name {
    font-family: "Montserrat", sans-serif;
    font-weight: 800;
    font-size: 28px;
    letter-spacing: 1px;
    color: var(--muted);
    margin: 0;
  }
  .identity .title {
    font-family: "Lato", sans-serif;
    font-weight: 400;
    font-size: 19px;
    color: var(--muted);
    margin: 2px 0 0;
  }
  .contacts {
    position: absolute;
    right: 30px;
    top: 300px;
    margin: 0;
    padding: 0;
    list-style: none;
    font-family: "Lato", sans-serif;
    font-size: 20px;
    color: var(--paper);
  }
  .contacts li {
    display: flex;
    justify-content: flex-end;
    align-items: center;
    gap: 10px;
    height: 35px;
  }
  .contacts .icon {
    width: 20px;
    height: 20px;
    flex: none;
  }
</style>
</head>
<body>

<section class="card card-back">
  <div class="texture" role="img" aria-label="Faint dark branch pattern behind the logo"></div>
  <div class="wordmark">BELLHAVEN</div>
</section>

<section class="card card-front">
  <svg class="wave" viewBox="0 0 760 434" width="760" height="434" aria-hidden="true">
    <path d="M0,276 C220,296 360,306 450,206 C540,106 640,126 760,116 L760,434 L0,434 Z" fill="var(--ink)"/>
    <path d="M0,290 C220,310 360,320 450,220 C540,120 640,140 760,130 L760,434 L0,434 Z" fill="var(--paper)"/>
    <path d="M0,306 C220,326 360,336 450,236 C540,136 640,156 760,146 L760,434 L0,434 Z" fill="var(--ink)"/>
  </svg>

  <div class="wordmark">BELLHAVEN</div>

  <div class="identity">
    <p class="name">LIORA QUENBY</p>
    <p class="title">Chief Financial Officer</p>
  </div>

  <ul class="contacts">
    <li>780-555-0142
      <svg class="icon" viewBox="0 0 24 24" aria-hidden="true"><path fill="var(--paper)" d="M6.6 10.8a15 15 0 0 0 6.6 6.6l2.2-2.2c.3-.3.7-.4 1-.2 1.1.4 2.3.6 3.6.6.6 0 1 .4 1 1V20c0 .6-.4 1-1 1A17 17 0 0 1 3 4c0-.6.4-1 1-1h3.5c.6 0 1 .4 1 1 0 1.3.2 2.5.6 3.6.1.3 0 .7-.2 1z"/></svg>
    </li>
    <li>lioraquenby@bellhavengroup.example
      <svg class="icon" viewBox="0 0 24 24" aria-hidden="true"><rect x="2" y="5" width="20" height="14" fill="var(--paper)"/><path d="M2 5l10 8 10-8" fill="none" stroke="var(--ink)" stroke-width="1.6"/></svg>
    </li>
    <li>www.bellhavengroup.example
      <svg class="icon" viewBox="0 0 24 24" aria-hidden="true"><circle cx="12" cy="12" r="10" fill="var(--paper)"/><g fill="none" stroke="var(--ink)" stroke-width="1.3"><ellipse cx="12" cy="12" rx="4.5" ry="10"/><path d="M2 12h20M4 7h16M4 17h16"/></g></svg>
    </li>
  </ul>
</section>

</body>
</html>
```